Northvale Strategy Partners Website Design

I need a website design for my new business consulting and executive coaching firm, Northvale Strategy Partners. We provide consultative services to business C-suites as well as personal coaching to executives. I have attached the logo with color scheme I have chosen. I would like the website to reflect professionalism and continue the color scheme in the logo.

Target Market(s)

Small to medium business and their executives; middle to upper income men and women in mid- to late career looking for significance

Industry/Entity Type

Business Consultant

Number of Pages Required

4 page

Requirements
Must have
• A homepage with prominent logo and way to contact for more information; an area on the homepage with easy to read, clear text to describe what the company does; a prominent area on the homepage for a tagline; a blog page that can be updated regularly, an "about us" page with biographical information; an "about us" page; a page detailing services offered
• The web design must match the logo colors and font that I have uploaded.
Nice to have
• A lighthouse picture in the background or header
Should not have
• A lot of text area on the homepage

```html
<!DOCTYPE html>
<html lang="en">
<head>
<meta charset="utf-8">
<title>Northvale Strategy Partners</title>
<link rel="stylesheet" href="https://fonts.googleapis.com/css2?family=Roboto+Slab:wght@400&family=Roboto+Condensed:wght@400&family=Arimo:wght@400&display=swap">
<style>
  :root {
    --navy: #1e3170;
    --navy-text: #25397a;
    --crimson: #7a1212;
    --white: #ffffff;
    --ink: #111111;
    --card-light: rgba(240, 242, 245, 0.88);
    --card-mid: rgba(200, 202, 206, 0.72);
    --card-grey: rgba(150, 150, 152, 0.85);
    --button-grey: #666666;
    --ring: #d9d9d9;
  }
  * { box-sizing: border-box; margin: 0; padding: 0; }
  html, body { width: 1200px; height: 825px; overflow: hidden; }
  body { position: relative; font-family: "Arimo", Arial, sans-serif; background: #1b2740; }

  .hero-photo {
    position: absolute; inset: 0 0 45px 0;
    background:
      radial-gradient(ellipse 520px 300px at 820px 470px, rgba(235,240,246,0.95), rgba(235,240,246,0) 100%),
      radial-gradient(ellipse 700px 420px at 560px 380px, rgba(170,190,210,0.9), rgba(170,190,210,0) 100%),
      linear-gradient(180deg, #1d2c48 0%, #3d5576 35%, #7e93ad 60%, #2a3342 85%, #15181e 100%);
  }
  .hero-photo::after {
    content: ""; position: absolute; inset: 0;
    background: linear-gradient(160deg, rgba(0,0,0,0) 55%, rgba(10,10,12,0.85) 80%);
  }

  .brand { position: absolute; left: 163px; top: 40px; display: flex; align-items: center; gap: 10px; }
  .brand-mark { width: 30px; height: 30px; border-radius: 50%; background: var(--white); flex: none; }
  .brand-name { font-family: "Roboto Slab", Georgia, serif; font-size: 20px; line-height: 24px; color: var(--white); width: 150px; }

  .contact-phone { position: absolute; left: 880px; top: 22px; display: flex; align-items: center; gap: 16px;
    font-family: "Roboto Condensed", Arial, sans-serif; font-size: 20px; color: var(--white); letter-spacing: 0.5px; }

  .main-nav { position: absolute; right: 160px; top: 69px; display: flex; gap: 0; }
  .main-nav a { font-family: "Roboto Slab", Georgia, serif; font-size: 14px; color: var(--white); text-decoration: none;
    height: 23px; line-height: 23px; padding: 0 13px; margin-left: 6px; }
  .main-nav a.is-active { background: var(--navy); }

  .tagline { position: absolute; left: 161px; top: 267px; font-family: "Roboto Slab", Georgia, serif; font-size: 32px;
    line-height: 45px; color: var(--navy-text); text-shadow: 0 0 8px rgba(255,255,255,0.6); }

  .feature { position: absolute; top: 588px; width: 272px; height: 192px; text-align: center; }
  .feature--about { left: 160px; background: var(--card-light); }
  .feature--services { left: 465px; background: var(--card-mid); }
  .feature--inquiry { left: 767px; background: var(--card-grey); }
  .feature-icon { position: absolute; left: 76px; top: -78px; width: 120px; height: 120px; border-radius: 50%;
    border: 5px solid var(--ring); background: var(--navy); display: flex; align-items: center; justify-content: center; }
  .feature--about .feature-icon { background: #7a0f0f; border-color: var(--navy); }
  .feature-title { margin-top: 50px; font-family: "Roboto Condensed", Arial, sans-serif; font-size: 20px; font-weight: 400; color: var(--ink); }
  .feature-text { margin: 8px auto 0; width: 250px; font-size: 11.5px; line-height: 18.5px; color: var(--ink); }
  .feature-button { position: absolute; left: 84px; top: 146px; width: 104px; height: 31px; }
  .feature--services .feature-button, .feature--inquiry .feature-button { left: 86px; }
  .feature-button span { position: absolute; left: 9px; top: 0; line-height: 31px; font-family: "Roboto Condensed", Arial, sans-serif;
    font-size: 14px; color: var(--white); letter-spacing: 0.3px; }

  .site-footer { position: absolute; left: 0; bottom: 0; width: 1200px; height: 45px; background: var(--crimson);
    display: flex; align-items: center; justify-content: space-between; padding: 0 163px 0 175px; }
  .social { display: flex; align-items: center; gap: 6px; font-family: "Roboto Condensed", Arial, sans-serif; font-size: 15px; color: var(--white); }
  .social-label { margin-right: 6px; }
  .social-dot { width: 28px; height: 28px; border-radius: 50%; background: var(--white); }
  .copyright { font-size: 12.5px; color: var(--white); }
</style>
</head>
<body>
  <div class="hero-photo" role="img" aria-label="Silhouette of one climber reaching down to help another up a mountain peak against a blue cloudy sky"></div>

  <header>
    <div class="brand">
      <span class="brand-mark"></span>
      <span class="brand-name">Northvale Strategy Partners</span>
    </div>
    <div class="contact-phone">
      <svg width="30" height="30" viewBox="0 0 30 30" aria-hidden="true">
        <circle cx="15" cy="15" r="13.5" fill="none" stroke="#fff" stroke-width="2"/>
        <path d="M11 8 l3 0 1 4 -2 1.5 c1 2.5 2.5 4 4.5 4.5 l1.5 -2 4 1 0 3 c-6 1 -12 -5 -12 -12z" fill="none" stroke="#fff" stroke-width="1.6" stroke-linejoin="round"/>
      </svg>
      <span>555-014-2368</span>
    </div>
    <nav class="main-nav">
      <a class="is-active" href="#">HOME</a>
      <a href="#">ABOUT US</a>
      <a href="#">SERVICES</a>
      <a href="#">BLOG</a>
      <a href="#">CONTACT US</a>
    </nav>
  </header>

  <h1 class="tagline" style="font-weight:400">We Are A Firm&nbsp; Providing<br>Business Consulting And<br>Executive Coaching</h1>

  <section class="feature feature--about">
    <div class="feature-icon"></div>
    <h2 class="feature-title">About Us</h2>
    <p class="feature-text">Lorem ipsum dolor sit amet, consectetuer into euismod tincidunt ut laoreet dolore magnain aliquam erat volutpat.</p>
    <a class="feature-button" href="#">
      <svg width="104" height="31" viewBox="0 0 104 31" aria-hidden="true"><path d="M0 0 H90 L104 15.5 L90 31 H0z" fill="#1e3170"/></svg>
      <span>READ MORE</span>
    </a>
  </section>

  <section class="feature feature--services">
    <div class="feature-icon">
      <svg width="60" height="60" viewBox="0 0 60 60" aria-hidden="true" fill="none" stroke="#fff" stroke-width="2">
        <rect x="6" y="4" width="48" height="30" rx="3"/>
        <path d="M40 26 v-8 M45 26 v-12 M50 26 v-6"/>
        <circle cx="15" cy="46" r="4" fill="#fff"/><circle cx="30" cy="46" r="4" fill="#fff"/><circle cx="45" cy="46" r="4" fill="#fff"/>
        <path d="M8 58 q7 -9 14 0z M23 58 q7 -9 14 0z M38 58 q7 -9 14 0z" fill="#fff"/>
      </svg>
    </div>
    <h2 class="feature-title">Services We Provide</h2>
    <p class="feature-text">Lorem ipsum dolor sit amet, consectetuer into euismod tincidunt ut laoreet dolore magnain aliquam erat volutpat.</p>
    <a class="feature-button" href="#">
      <svg width="104" height="31" viewBox="0 0 104 31" aria-hidden="true"><path d="M0 0 H90 L104 15.5 L90 31 H0z" fill="#666"/></svg>
      <span>READ MORE</span>
    </a>
  </section>

  <section class="feature feature--inquiry">
    <div class="feature-icon">
      <svg width="60" height="60" viewBox="0 0 30 30" aria-hidden="true">
        <circle cx="15" cy="15" r="13.5" fill="none" stroke="#fff" stroke-width="1.6"/>
        <path d="M11 8 l3 0 1 4 -2 1.5 c1 2.5 2.5 4 4.5 4.5 l1.5 -2 4 1 0 3 c-6 1 -12 -5 -12 -12z" fill="none" stroke="#fff" stroke-width="1.4" stroke-linejoin="round"/>
      </svg>
    </div>
    <h2 class="feature-title">QUICK INQUIRY</h2>
    <p class="feature-text">Lorem ipsum dolor sit amet, consectetuer into euismod tincidunt ut laoreet dolore magnain aliquam erat volutpat.</p>
    <a class="feature-button" href="#">
      <svg width="116" height="31" viewBox="0 0 116 31" aria-hidden="true"><path d="M0 0 H102 L116 15.5 L102 31 H0z" fill="#666"/></svg>
      <span>GET STARTED</span>
    </a>
  </section>

  <footer class="site-footer">
    <div class="social">
      <span class="social-label">FOLLOW US</span>
      <span class="social-dot"></span><span class="social-dot"></span><span class="social-dot"></span><span class="social-dot"></span>
    </div>
    <p class="copyright">© 2016 Northvale Strategy Partners All Rights Reserved</p>
  </footer>
</body>
</html>
```